real esate business card with company logo and name

we need a business card design for a real esate company

The company name is Walsh & Brand Pty Ltd, and we have our logo designed and will upload. We want classic or moden feel. Black or white background. looks more textured. Should include folowinginformations
Owen Walsh and Lucy Brand
Sales Agents & Onsite Manager
p: 07 5948 2063
F: 07 5948 2174
M:0431 857 219
3/42 Marlow Crescent, FERNLEA QLD 4213

We want this business card looks professonal. Thank you in advance.

Industry/Entity Type

Real Estate Agent

Contact Information for Business Card

Owen Walsh and Lucy Brand
Onsite Manager & Sales Agents
p: 07 5948 2063
M:0431 857 219

Font styles to use
Serif

Colors
000000
fbfbfb
333333
959595

Requirements
Must have
• company logo and name, black or white back ground

```html
<!DOCTYPE html>
<html lang="en">
<head>
<meta charset="utf-8">
<title>Walsh &amp; Brand Pty Ltd — Business Card</title>
<link href="https://fonts.googleapis.com/css2?family=Lato:wght@400;700&display=swap" rel="stylesheet">
<style>
  :root {
    --black: #000000;
    --white: #f4f4f4;
    --dark: #333333;
    --grey: #959595;
    --stage: #2e2e2e;
    --type: #fbfbfb;
  }
  * { margin: 0; padding: 0; box-sizing: border-box; }
  html, body {
    width: 1200px; height: 1086px; overflow: hidden;
    background: var(--stage);
    font-family: "Lato", sans-serif;
  }
  .card {
    position: absolute; left: 254px; width: 677px; height: 387px;
    box-shadow: 0 4px 10px rgba(0,0,0,.45);
  }
  .card--front { top: 126px; background: var(--black); }
  .card--back  { top: 586px; background: var(--black); }

  .brand-panel {
    position: absolute; left: 0; top: 0; width: 339px; height: 100%;
    background: var(--white);
  }
  .brand-panel::after {
    content: ""; position: absolute; right: -20px; top: 94px;
    border-top: 16px solid transparent; border-bottom: 16px solid transparent;
    border-left: 20px solid var(--white);
  }
  .brand {
    position: absolute; left: 0; right: 0; text-align: center;
    font-weight: 400; letter-spacing: 1px; font-size: 14px;
  }
  .brand__mark { display: block; margin: 0 auto 26px; background: var(--grey); }
  .brand-panel .brand { top: 112px; color: var(--dark); }
  .brand-panel .brand__mark { width: 110px; height: 110px; }
  .card--back .brand { top: 116px; color: var(--grey); font-size: 16px; }
  .card--back .brand__mark { width: 118px; height: 118px; background: #6e6e6e; }

  .contact {
    position: absolute; left: 393px; top: 94px; color: var(--type);
  }
  .contact__name { font-weight: 700; font-size: 29px; line-height: 1.1; }
  .contact__role { font-size: 21px; line-height: 1.2; margin-bottom: 18px; }
  .contact__lines { list-style: none; font-size: 19px; line-height: 23px; }
  .contact__lines li { display: flex; align-items: center; gap: 5px; }
  .contact__lines svg { width: 14px; height: 14px; fill: var(--type); flex: none; }
  .contact__address { margin-top: 16px; font-size: 17px; line-height: 22px; margin-left: -3px; }
</style>
</head>
<body>
  <section class="card card--front">
    <div class="brand-panel">
      <div class="brand"><span class="brand__mark"></span>WALSH &amp; BRAND PTY LTD.</div>
    </div>
    <div class="contact">
      <h1 class="contact__name">Owen Walsh</h1>
      <p class="contact__role">Sales Agents</p>
      <ul class="contact__lines">
        <li><svg viewBox="0 0 14 14" aria-hidden="true"><path d="M4 0h6a1 1 0 0 1 1 1v12a1 1 0 0 1-1 1H4a1 1 0 0 1-1-1V1a1 1 0 0 1 1-1zm.5 1.5v9h5v-9zM7 11.5a.8.8 0 1 0 0 1.6.8.8 0 0 0 0-1.6z"/></svg>0431 857 219</li>
        <li><svg viewBox="0 0 14 14" aria-hidden="true"><path d="M0 5c0-2 3-3 7-3s7 1 7 3v1h-3.5V4.5h-7V6H0zM3 7h8l2 6H1zm4 1.5a2 2 0 1 0 0 4 2 2 0 0 0 0-4z"/></svg>07 5948 2063</li>
        <li><svg viewBox="0 0 14 14" aria-hidden="true"><path d="M3 1h8v4H3zM1 6h12v5h-2V9H3v2H1zM4 10h6v3H4z"/></svg>07 5948 2174</li>
      </ul>
      <p class="contact__address">3/42 Marlow Crescent<br>FERNLEA QLD 4213</p>
    </div>
  </section>

  <section class="card card--back">
    <div class="brand"><span class="brand__mark"></span>WALSH &amp; BRAND PTY LTD.</div>
  </section>
</body>
</html>
```